Business cards to launch an education platform

Hi,
I am looking at having new business cards designed.
I am a startup, developing a web platform for schools and university, the education world. It's an online assessment system.
I would like a card that looks classy, and that is using the colors and the font of my logo.

I have attached:
1) my logo
2) A business card that I have designed quickly so you can have all the information required in the card, but I really don't like it.
3) The font that I am using (Lato Regular) to design my web platform
4) Some screenshots of my web platform so you can have a look at the style that I have.

Target Market(s)

Major market: Education system: Schools and university
Minor markets: Business in general

Industry/Entity Type

Business

Contact Information for Business Card

Clara Fenwick
Director

M: 0437 518 902
E: clara.fenwick@amberLoomSystems.com.au

Requirements
Must have
• The colors of my logo

```html
<!DOCTYPE html>
<html lang="en">
<head>
<meta charset="utf-8">
<title>Amber Loom Systems – Business Cards</title>
<link rel="stylesheet" href="https://fonts.googleapis.com/css2?family=Lato:wght@400;700&display=swap">
<style>
  :root {
    --backdrop: #e9e6e1;
    --navy: #0c4478;
    --navy-deep: #083763;
    --sky: #29a9e0;
    --ink: #1e4f80;
    --grey-text: #555b62;
    --white: #ffffff;
  }
  * { box-sizing: border-box; margin: 0; padding: 0; }
  html, body {
    width: 1200px; height: 950px; overflow: hidden;
    background: var(--backdrop);
    font-family: "Lato", sans-serif;
  }
  .canvas { position: relative; width: 1200px; height: 950px; }
  .card {
    position: absolute; width: 560px; height: 342px;
    border-radius: 4px;
    box-shadow: 0 14px 30px rgba(0,0,0,0.18);
    overflow: hidden;
  }
  /* Front */
  .card-front {
    left: 70px; top: 100px;
    background: linear-gradient(135deg, var(--navy) 0%, var(--navy-deep) 100%);
    color: var(--white);
  }
  .card-front .brand {
    position: absolute; left: 110px; top: 120px;
    display: flex; align-items: center; gap: 18px;
  }
  .brand-square { width: 54px; height: 54px; background: var(--white); flex: none; }
  .card-front .brand-name {
    font-size: 30px; font-weight: 400; letter-spacing: 2px; color: var(--white);
  }
  .card-front .website {
    position: absolute; left: 0; right: 0; top: 250px;
    text-align: center; font-size: 15px; letter-spacing: 0.5px; padding-left: 60px;
  }
  /* Back */
  .card-back { left: 570px; top: 500px; background: var(--white); }
  .card-back .brand {
    position: absolute; left: 40px; top: 120px; width: 170px;
    display: flex; flex-direction: column; align-items: flex-start; gap: 12px;
  }
  .card-back .brand-square { width: 50px; height: 50px; background: var(--sky); }
  .card-back .brand-name {
    font-size: 24px; line-height: 1.2; font-weight: 400; letter-spacing: 1.5px; color: var(--ink);
  }
  .contact {
    position: absolute; right: 36px; top: 70px; text-align: right;
  }
  .contact .person { font-size: 22px; font-weight: 700; color: var(--ink); }
  .contact .role { font-size: 14px; color: var(--sky); margin-top: 2px; }
  .contact .lines { margin-top: 34px; font-size: 14px; color: var(--grey-text); }
  .contact .line {
    display: flex; justify-content: flex-end; align-items: center; gap: 10px;
    margin-bottom: 8px; white-space: nowrap;
  }
  .contact .line svg { width: 14px; height: 14px; flex: none; }
</style>
</head>
<body>
<main class="canvas">
  <section class="card card-front" aria-label="Business card front">
    <div class="brand">
      <span class="brand-square"></span>
      <span class="brand-name">Amber Loom Systems</span>
    </div>
    <p class="website">www.amberLoomSystems.com.au</p>
  </section>

  <section class="card card-back" aria-label="Business card back">
    <div class="brand">
      <span class="brand-square"></span>
      <span class="brand-name">Amber Loom<br>Systems</span>
    </div>
    <div class="contact">
      <p class="person">Clara Fenwick</p>
      <p class="role">Director</p>
      <div class="lines">
        <p class="line">
          <span>0437 518 902</span>
          <svg viewBox="0 0 14 14" aria-hidden="true">
            <rect x="3" y="0.5" width="8" height="13" rx="1.5" fill="none" stroke="var(--ink)" stroke-width="1.4"/>
            <circle cx="7" cy="11" r="0.9" fill="var(--ink)"/>
          </svg>
        </p>
        <p class="line">
          <span>clara.fenwick@amberLoomSystems.com.au</span>
          <svg viewBox="0 0 14 14" aria-hidden="true">
            <rect x="0.5" y="3" width="13" height="9" fill="var(--ink)"/>
            <path d="M0.5 3 L7 8 L13.5 3" fill="none" stroke="var(--white)" stroke-width="1"/>
          </svg>
        </p>
      </div>
    </div>
  </section>
</main>
</body>
</html>
```